New Business Card Design

We would like to refresh our business cards and make them look better. We are an IT company specialising in Cloud Services, IT Managed Services, software and hardware. I have attached a PSD of our current design. Also attached our logo.
Updates

I have uploaded all new logos in EPS format.

Can you please edit all designs to include a job title for Marcus Hollis, eg. General Manager

Industry/Entity Type

Software

Colors
ffffff

Requirements
Must have
• Please use white background.
Should not have
• Black background

```html
<!DOCTYPE html>
<html lang="en">
<head>
<meta charset="utf-8">
<title>Northvale Technology – Business Cards</title>
<link rel="stylesheet" href="https://fonts.googleapis.com/css2?family=Open+Sans:wght@400;600;700&display=swap">
<style>
  :root {
    --stage: #ecebe8;
    --card-white: #f4f4f3;
    --card-silver: #e6e6e5;
    --brand-red: #c0382b;
    --ink: #2b2b2b;
    --ink-soft: #555555;
    --white: #ffffff;
  }
  * { box-sizing: border-box; margin: 0; padding: 0; }
  html, body {
    width: 1200px; height: 720px; overflow: hidden;
    background: var(--stage);
    font-family: "Open Sans", Arial, sans-serif;
  }
  .canvas { position: relative; width: 1200px; height: 720px; }

  .card {
    position: absolute; top: 205px;
    width: 540px; height: 310px;
    border-radius: 4px; overflow: hidden;
    box-shadow: 0 6px 18px rgba(0,0,0,.14);
  }
  .card--front { left: 40px; background: linear-gradient(160deg, var(--white), var(--card-white)); }
  .card--back  { left: 620px; background: linear-gradient(160deg, var(--white), var(--card-silver)); }

  /* company name, set plainly in the card's text font */
  .company-name {
    color: var(--ink);
    font-weight: 400;
    letter-spacing: 0;
    white-space: nowrap;
    line-height: 1;
  }
  .card--front .company-name {
    position: absolute; top: 48px; left: 120px;
    font-size: 28px;
  }
  .card--back .company-name {
    position: absolute; top: 112px; left: 0; right: 0;
    text-align: center;
    font-size: 38px;
  }

  .contact-band {
    position: absolute; left: 0; right: 0; top: 122px; bottom: 0;
    background: var(--brand-red); color: var(--white);
    padding: 22px 0 0 30px;
  }
  .person { font-size: 18px; }
  .person__name { font-weight: 700; }
  .person__role { font-weight: 400; font-size: 15px; }
  .contact-list { list-style: none; margin-top: 14px; }
  .contact-list li {
    display: flex; align-items: center; gap: 10px;
    font-size: 13.5px; line-height: 1; margin-bottom: 9px;
  }
  .contact-list svg { width: 15px; height: 15px; flex: none; }

  .tagline {
    position: absolute; left: 0; right: 0; bottom: 36px;
    text-align: center; color: var(--ink-soft);
    font-size: 15px; line-height: 1.45;
  }
</style>
</head>
<body>
<main class="canvas">

  <section class="card card--front" aria-label="Business card front">
    <p class="company-name">Northvale Technology</p>

    <div class="contact-band">
      <p class="person"><span class="person__name">Marcus Hollis,</span> <span class="person__role">General Manager</span></p>
      <ul class="contact-list">
        <li>
          <svg viewBox="0 0 16 16" aria-hidden="true"><circle cx="8" cy="8" r="7.5" fill="#fff"/><path d="M5.2 4.2l1.5-.3.8 2-1 .8c.5 1.1 1.3 1.9 2.4 2.4l.8-1 2 .8-.3 1.5c-3.4.2-6.4-2.8-6.2-6.2z" fill="#c0382b"/></svg>
          07 3555 0148
        </li>
        <li>
          <svg viewBox="0 0 16 16" aria-hidden="true"><circle cx="8" cy="8" r="7.5" fill="#fff"/><rect x="5.5" y="3.5" width="5" height="9" rx="1" fill="#c0382b"/><rect x="6.4" y="4.6" width="3.2" height="5.4" fill="#fff"/></svg>
          0400 555 219
        </li>
        <li>
          <svg viewBox="0 0 16 16" aria-hidden="true"><circle cx="8" cy="8" r="7.5" fill="#fff"/><rect x="4" y="5" width="8" height="6" fill="#c0382b"/><path d="M4 5l4 3.3L12 5" fill="none" stroke="#fff" stroke-width=".9"/></svg>
          mhollis@northvaleit.com.au
        </li>
        <li>
          <svg viewBox="0 0 16 16" aria-hidden="true"><circle cx="8" cy="8" r="7.5" fill="#fff"/><g fill="none" stroke="#c0382b" stroke-width=".9"><circle cx="8" cy="8" r="4.3"/><ellipse cx="8" cy="8" rx="1.9" ry="4.3"/><path d="M3.7 8h8.6"/></g></svg>
          www.northvaleit.com.au
        </li>
      </ul>
    </div>
  </section>

  <section class="card card--back" aria-label="Business card back">
    <p class="company-name">Northvale Technology</p>
    <p class="tagline">We are an IT company specializing in Cloud Services<br>IT Managed Services, software and hardware</p>
  </section>

</main>
</body>
</html>
```